Income Tax Flyer - Updates Needed

Just need to update this flyer design and give it a new look. We would like to keep all the same wording but make it stand out a little more. Our selling point is the "Same Day Tax Advance up to $6,000"

Lending, Small Loans, Tax Services, Title Loans, Personal Loans

```html
<!DOCTYPE html>
<html lang="en">
<head>
<meta charset="utf-8">
<title>Tax Advance Flyer</title>
<link rel="stylesheet" href="https://fonts.googleapis.com/css2?family=Fira+Sans:wght@700;800&family=Source+Sans+3:wght@400;600;700&family=Roboto:wght@400;500;700&display=swap">
<style>
  :root {
    --green: #2b5a3e;
    --green-deep: #255a39;
    --red: #c4373b;
    --red-dark: #a92c30;
    --ink-white: #ffffff;
    --page: #efefef;
    --rule: #d9d9d9;
  }
  * { box-sizing: border-box; margin: 0; padding: 0; }
  html, body { width: 1200px; height: 752px; overflow: hidden; }
  body { background: var(--page); font-family: "Source Sans 3", sans-serif; position: relative; }

  .flyer {
    position: absolute; left: 355px; top: 26px;
    width: 490px; height: 700px;
    background: #fff;
    box-shadow: 0 14px 30px rgba(0,0,0,.18);
    overflow: hidden;
  }

  .brand {
    position: absolute; top: 34px; left: 0; width: 100%;
    text-align: center;
  }
  .brand-name {
    display: inline-flex; align-items: center; gap: 7px;
    font-family: "Source Sans 3", sans-serif; font-weight: 600;
    font-size: 19px; color: var(--green); letter-spacing: .3px;
  }
  .brand-dot { width: 12px; height: 12px; border-radius: 50%; background: var(--red); }

  .brand-rule {
    position: absolute; top: 92px; left: 46px; width: 398px;
    height: 1px; background: var(--rule);
  }

  .headline { position: absolute; left: 0; width: 100%; text-align: center; }
  .headline-lead { top: 109px; font-size: 35px; color: var(--red); font-weight: 400; line-height: 1; }
  .headline-amount {
    top: 142px; font-family: "Fira Sans", sans-serif; font-weight: 800;
    font-size: 54px; color: var(--green-deep); line-height: 1; letter-spacing: -.5px;
  }
  .headline-today {
    top: 206px; font-family: "Fira Sans", sans-serif; font-weight: 800;
    font-size: 33px; color: var(--red); line-height: 1;
  }

  .advance-band { position: absolute; top: 259px; left: 0; width: 490px; height: 80px; }
  .advance-text {
    position: absolute; top: 265px; left: 0; width: 100%;
    text-align: center; color: var(--ink-white); line-height: 1.1;
  }
  .advance-lead { font-size: 27px; font-weight: 400; display: block; }
  .advance-strong { font-family: "Fira Sans", sans-serif; font-weight: 700; font-size: 25px; display: block; margin-top: 2px; }

  .photo {
    position: absolute; top: 327px; left: 0; width: 490px; height: 221px;
    background: linear-gradient(90deg, #6f6a62 0%, #a7a79a 14%, #c9cfb6 30%, #eae7dc 52%, #f3efe6 62%, #c8b77f 80%, #b08d4c 100%);
    z-index: 0;
  }
  .advance-band { z-index: 1; }
  .advance-text { z-index: 2; }

  .features {
    position: absolute; top: 492px; left: 0; width: 490px; height: 128px;
    display: flex; justify-content: space-around; padding: 0 20px;
  }
  .feature { width: 140px; text-align: center; }
  .feature-badge {
    width: 78px; height: 78px; border-radius: 50%; background: #fff;
    margin: 0 auto; display: flex; align-items: center; justify-content: center;
  }
  .feature-label {
    font-family: "Roboto", sans-serif; color: var(--green-deep);
    font-size: 12px; line-height: 1.25; margin-top: 12px; letter-spacing: .2px;
    min-height: 30px; display: flex; flex-direction: column; justify-content: center;
  }
  .feature-label b { font-weight: 700; }

  .contact-bar {
    position: absolute; left: 0; bottom: 0; width: 490px; height: 71px;
    background: var(--red); color: var(--ink-white);
    display: flex; align-items: center;
  }
  .contact-phone-icon { position: absolute; left: 3px; top: 2px; }
  .contact-call {
    position: relative; margin-left: 30px; width: 120px;
    font-family: "Source Sans 3", sans-serif; font-weight: 700; line-height: .95;
  }
  .contact-call span { display: block; font-size: 16px; }
  .contact-call strong { display: block; font-size: 27px; }
  .contact-number { margin-left: 21px; font-size: 22px; font-weight: 700; width: 170px; }
  .contact-address { margin-left: 18px; font-size: 13px; font-weight: 700; line-height: 1.35; }
</style>
</head>
<body>
  <article class="flyer">
    <header class="brand">
      <span class="brand-name"><span class="brand-dot"></span>Ledgerline Financial Group</span>
    </header>
    <div class="brand-rule"></div>

    <p class="headline headline-lead">Apply here for</p>
    <p class="headline headline-amount">$5000 - $6000</p>
    <p class="headline headline-today">TODAY!</p>

    <div class="photo" role="img" aria-label="Photo of a smiling businesswoman in a white blazer in a bright office"></div>

    <svg class="advance-band" viewBox="0 0 490 80" aria-hidden="true">
      <path d="M0 0 H490 V67 Q245 80 0 68 Z" fill="var(--green)"/>
    </svg>
    <p class="advance-text">
      <span class="advance-lead">File your taxes and apply for an</span>
      <span class="advance-strong">EASY ADVANCE!</span>
    </p>

    <section class="features">
      <div class="feature">
        <div class="feature-badge">
          <svg width="48" height="48" viewBox="0 0 48 48" fill="none" stroke="var(--green-deep)" stroke-width="1.8">
            <circle cx="24" cy="27" r="17"/><circle cx="24" cy="27" r="13"/>
            <path d="M20 6h8M24 6v4M8 12l3 3M40 12l-3 3"/>
            <text x="24" y="33" text-anchor="middle" font-family="Roboto, sans-serif" font-size="16" fill="var(--green-deep)" stroke="none">$</text>
          </svg>
        </div>
        <p class="feature-label"><span>AVAILABLE IN</span><b>24 HOURS OR LESS</b></p>
      </div>
      <div class="feature">
        <div class="feature-badge">
          <svg width="48" height="48" viewBox="0 0 48 48" fill="none" stroke="var(--green-deep)" stroke-width="1.8">
            <path d="M37 26A16 16 0 1 0 24 40"/>
            <text x="21" y="29" text-anchor="middle" font-family="Roboto, sans-serif" font-size="16" fill="var(--green-deep)" stroke="none">$</text>
            <path d="M29 44v-6l-3-3a1.5 1.5 0 0 1 2-2l2 2V24a1.6 1.6 0 0 1 3 0v7l5 1a3 3 0 0 1 2 3l-1 9"/>
          </svg>
        </div>
        <p class="feature-label"><span>CHOOSE YOUR</span><b>LOAN AMOUNT</b></p>
      </div>
      <div class="feature">
        <div class="feature-badge">
          <svg width="56" height="48" viewBox="0 0 56 48" fill="none" stroke="var(--green-deep)" stroke-width="1.8">
            <circle cx="34" cy="24" r="15"/><circle cx="34" cy="24" r="11"/>
            <path d="M4 26h14M8 31h12M12 36h10M2 21h10"/>
            <text x="34" y="30" text-anchor="middle" font-family="Roboto, sans-serif" font-size="15" fill="var(--green-deep)" stroke="none">$</text>
          </svg>
        </div>
        <p class="feature-label"><span><b>QUICK</b> AND <b>EASY</b></span></p>
      </div>
    </section>

    <footer class="contact-bar">
      <svg class="contact-phone-icon" width="44" height="70" viewBox="0 0 44 70" aria-hidden="true">
        <rect x="2" y="2" width="40" height="68" rx="7" fill="var(--red-dark)"/>
        <rect x="7" y="9" width="30" height="46" rx="2" fill="var(--red)"/>
        <circle cx="22" cy="62" r="3" fill="var(--red)"/>
      </svg>
      <p class="contact-call"><span>CONTACT US</span><strong>TODAY!</strong></p>
      <p class="contact-number">Phone Number</p>
      <p class="contact-address">Address line 1<br>Address line 2<br>Address line 3</p>
    </footer>
  </article>
</body>
</html>
```